Business Card Design For Marketing Agnecy LVP

Need business card design for marketing agency.

Doug Fenwick
President, CEO
1-555-302-4196
doug@boldpromoperksgroup.example
www.BoldPromoPerksGroup.example

Back Side:
Boost Sales Using Rewards, Incentives & Giveaways
Get A Free Sample Package

Target Market(s)

B2B

Industry/Entity Type

Marketing

Contact Information for Business Card

Doug Fenwick
President, CEO
1-555-302-4196

Back Side:
Get A Free Sample Package

Please note that my current url is OLD DESIGN. I am working on new design and want the business card to match color themes at least on new site. Here is the demo link for new site so you can see the colors I use, etc.

http://layoutcratehub.example/kq/doug/lvp_final/index.html

Requirements
Must have
• Please note that my current url is OLD DESIGN. I am working on new design and want the business card to match color themes at least on new site. Here is the demo link for new site so you can see the colors I use, etc.

Nice to have

Should not have

```html
<!DOCTYPE html>
<html lang="en">
<head>
<meta charset="utf-8">
<title>LVP Business Card</title>
<link href="https://fonts.googleapis.com/css2?family=Montserrat:wght@600;700;800&family=Roboto+Condensed:wght@400&display=swap" rel="stylesheet">
<style>
  :root {
    --backdrop: #3a3a3c;
    --card: #1c1c1e;
    --emboss: #2c2c2e;
    --emboss-light: #4a4a4d;
    --brand-blue: #2d65a8;
    --brand-green: #4cb838;
    --ink-light: #ffffff;
    --icon: #9a9a9e;
  }
  * { margin: 0; padding: 0; box-sizing: border-box; }
  html, body {
    width: 799px; height: 1200px; overflow: hidden;
    background: var(--backdrop);
  }
  .sheet {
    position: relative; width: 799px; height: 1200px;
    display: flex; flex-direction: column; align-items: center; justify-content: space-around;
    padding: 60px 0;
  }
  .card {
    position: relative; width: 620px; height: 354px;
    background: var(--card); overflow: hidden;
    box-shadow: 0 14px 30px rgba(0,0,0,0.45);
  }
  /* front */
  .card-front { display: flex; align-items: center; justify-content: center; }
  .front-mark {
    display: flex; align-items: flex-start; gap: 10px;
  }
  .front-name {
    font-family: "Montserrat", sans-serif; font-weight: 800;
    font-size: 150px; line-height: 1; letter-spacing: -4px;
    color: var(--emboss);
    text-shadow: 0 1px 0 var(--emboss-light);
  }
  .front-dot {
    width: 26px; height: 26px; border-radius: 50%;
    background: var(--emboss); margin-top: 18px;
  }
  /* back */
  .back-mark {
    position: absolute; left: 40px; top: 36px;
    display: flex; align-items: flex-start; gap: 6px;
  }
  .back-name {
    font-family: "Montserrat", sans-serif; font-weight: 800;
    font-size: 52px; line-height: 1; letter-spacing: -1px;
    color: var(--brand-blue);
  }
  .back-dot {
    width: 10px; height: 10px; border-radius: 50%;
    background: var(--brand-blue); margin-top: 4px;
  }
  .contact-list {
    position: absolute; left: 40px; top: 112px;
    list-style: none;
    font-family: "Roboto Condensed", sans-serif; font-size: 15px;
    color: var(--ink-light);
  }
  .contact-list li { display: flex; align-items: center; gap: 10px; height: 22px; }
  .contact-list svg { width: 12px; height: 12px; flex: none; }
  .waves { position: absolute; left: 0; top: 0; width: 620px; height: 354px; }
  .holder {
    position: absolute; right: 40px; bottom: 28px; text-align: right;
    color: var(--ink-light);
  }
  .holder-name {
    font-family: "Montserrat", sans-serif; font-weight: 700; font-size: 24px;
  }
  .holder-title {
    font-family: "Roboto Condensed", sans-serif; font-size: 16px; margin-top: 4px;
  }
</style>
</head>
<body>
<main class="sheet">
  <section class="card card-front" aria-label="Card front">
    <div class="front-mark">
      <span class="front-name">LVP</span>
      <span class="front-dot"></span>
    </div>
  </section>

  <section class="card card-back" aria-label="Card back">
    <svg class="waves" viewBox="0 0 620 354" aria-hidden="true">
      <path d="M0,212 C90,222 160,282 280,287 C400,292 500,232 620,202 L620,354 L0,354 Z" fill="var(--brand-blue)"/>
      <path d="M0,182 C100,192 170,257 290,264 C410,270 510,214 620,182 L620,194 C510,227 410,280 290,277 C170,272 100,212 0,197 Z" fill="var(--brand-green)"/>
    </svg>

    <div class="back-mark">
      <span class="back-name">LVP</span>
      <span class="back-dot"></span>
    </div>

    <ul class="contact-list">
      <li>
        <svg viewBox="0 0 12 12"><path d="M2.5 1 L4.5 1 L5.2 3.6 L4 4.6 C4.6 6 6 7.4 7.4 8 L8.4 6.8 L11 7.5 L11 9.5 C11 10.3 10.3 11 9.5 11 C5 11 1 7 1 2.5 C1 1.7 1.7 1 2.5 1 Z" fill="var(--icon)"/></svg>
        1-555-302-4196
      </li>
      <li>
        <svg viewBox="0 0 12 12"><rect x="0.5" y="2" width="11" height="8" fill="var(--icon)"/><path d="M0.5 2 L6 6.5 L11.5 2" fill="none" stroke="var(--card)" stroke-width="1"/></svg>
        doug@boldpromoperksgroup.example
      </li>
      <li>
        <svg viewBox="0 0 12 12"><circle cx="6" cy="6" r="5.2" fill="none" stroke="var(--icon)" stroke-width="1.2"/><ellipse cx="6" cy="6" rx="2.2" ry="5.2" fill="none" stroke="var(--icon)" stroke-width="1"/><path d="M0.8 6 H11.2" stroke="var(--icon)" stroke-width="1"/></svg>
        www.BoldPromoPerksGroup.example
      </li>
    </ul>

    <div class="holder">
      <p class="holder-name">Doug Fenwick</p>
      <p class="holder-title">President, CEO</p>
    </div>
  </section>
</main>
</body>
</html>
```